Consulting business card

*1) An Overview:* The business is simply a financial transaction wherein I
offer to provide advice to financial holders of commercial real estate
mortgages (which are sub-performing or non-performing), and said holders
are desirous of selling said mortgages which I will offer advice to said
holders in the purchase of said mortgages. Please note the attached copy
of a proposed line-by-line business card which starts with the 1st line
"RKW Advisory, LLC" with the 2nd line "Purchase of Commercial Mortgage
Loan" and the 3rd line "Sub-performing and Non-performing" is my desired
copy subject to any suggested changes. Please ignore the the copy below
the aforementioned proposed card/copy as it will be activated at a later
date.and advise
*2) The Target Market:* I contact and advise senior officers in banks,
insurance companies, and financial institutions such as CEOs, CFOs, COOs,
and Loan Mitigation Officers: the senior officers are tasked with the
removal of sub-performing and non-performing commercial real estate loans
from their real estate portfolios. The desired market is targeted at $1-10
million USD and located in the US.
*3) Design Specifics: *STYLE should be conservative and be representative
of the financial market contacts; COLOR might show a rich forest green
element, a gold foil accent, and subtle black printing, however,
alternatively, silver foil accent(s) with strong black print would seem in
harmony with the services offered, however, I would appreciate any artful
suggestions; IMAGERY should be subtle (no logo can be strong enough to make
an immediate impact): the quality should make the recipient feel he/she has
just met an experienced and competent financial adviser (I have over 55
years of successful financial and business experience).
720.217.6154davidfredrickjones@gmail.com

```html
<!DOCTYPE html>
<html lang="en">
<head>
<meta charset="utf-8">
<title>RKW Advisory, LLC – Business Card</title>
<link rel="stylesheet" href="https://fonts.googleapis.com/css2?family=Lora:wght@400;700&family=Arimo:wght@400&display=swap">
<style>
  :root {
    --forest: #05582f;
    --gold: #d8c23b;
    --paper: #ffffff;
    --ink: #111111;
    --page: #ecebe7;
  }
  html, body {
    margin: 0;
    padding: 0;
    width: 1200px;
    height: 826px;
    overflow: hidden;
    background: var(--page);
  }
  .card {
    position: relative;
    width: 1200px;
    height: 826px;
    background: var(--paper);
    overflow: hidden;
  }
  .card-bands {
    position: absolute;
    inset: 0;
    width: 100%;
    height: 100%;
  }
  .card-copy {
    position: absolute;
    left: 330px;
    width: 620px;
    top: 150px;
    text-align: center;
    color: var(--ink);
  }
  .company-name {
    margin: 0;
    font-family: "Lora", Georgia, serif;
    font-weight: 700;
    font-size: 64px;
    line-height: 1.1;
    letter-spacing: 1px;
  }
  .company-tagline {
    margin: 8px 0 0;
    font-family: "Arimo", Arial, sans-serif;
    font-size: 29px;
    line-height: 1.3;
  }
  .contact {
    margin-top: 80px;
  }
  .contact-name {
    margin: 0 0 18px;
    font-family: "Lora", Georgia, serif;
    font-weight: 400;
    font-size: 52px;
    letter-spacing: 1px;
  }
  .contact-line {
    margin: 0;
    font-family: "Arimo", Arial, sans-serif;
    font-size: 34px;
    line-height: 1.35;
  }
</style>
</head>
<body>
  <main class="card">
    <svg class="card-bands" viewBox="0 0 1200 826" aria-hidden="true">
      <path class="band-top" d="M0 0 H1200 V150 Q600 -40 0 150 Z" fill="var(--forest)"/>
      <path class="band-top-accent" d="M0 150 Q600 -40 1200 150" fill="none" stroke="var(--gold)" stroke-width="16"/>
      <path class="band-bottom" d="M0 826 H1200 V676 Q600 866 0 676 Z" fill="var(--forest)"/>
      <path class="band-bottom-accent" d="M0 676 Q600 866 1200 676" fill="none" stroke="var(--gold)" stroke-width="16"/>
    </svg>
    <section class="card-copy">
      <h1 class="company-name">RKW Advisory, LLC</h1>
      <p class="company-tagline">Purchase of Commercial Mortgage Loan<br>Sub-performing and Non-performing</p>
      <div class="contact">
        <h2 class="contact-name">Glen Marlow</h2>
        <p class="contact-line">555.304.8827</p>
        <p class="contact-line">tomasheraldwick@mailbox.example</p>
      </div>
    </section>
  </main>
</body>
</html>
```